Wren of Fabrics relaunch: brand, logo and website redesign

Wren of Fabrics www.wrenoffabrics.com is relaunching to focus on empowering style advice, e books and courses.
We need a new logo, brand identity and website which reflects this change.
The structure of the site and pages have been completed http://dev1.wrenoffabrics.com/
but we need to update the brand look and feel
Please read the full brief, uploaded, before submitting your designs.

Target Market(s)

Women, primarily aged 28-45, English speaking USA and UK
Ambitious and determined. Looking for solutions. Open to self-improvement.
Maybe not as confident with style and body image as other parts of their life.

Logo Text

Brand name Wren of Fabrics Strapline version 1: Unlock your personal best Strapline version 2: Unlock better Logo/graphical icon for use with/without text

Number of Pages Required

3 page

Font styles to use
Sans Serif

Requirements
Must have
• 1. Web designs for home page, a channel page and advice page (see attached brief)
Web designs must be consistent with new website design navigation, and page structure http://dev1.wrenoffabrics.com/
2. Web style guide to include colour palettes/system; web fonts, icons, illustrations and guidelines/examples free stock photography. see Mindmap upload for example of colour pallette we like.
Nice to have
• Ebook front covers
Quiz promotions
Course promotions
Other web pages
Social media pages eg Pagebook, Snapgrid,Chirpline
Should not have
• Paid photography or photos where don’t have the rights

```html
<!DOCTYPE html>
<html lang="en">
<head>
<meta charset="utf-8">
<title>Wren of Fabrics – About</title>
<link href="https://fonts.googleapis.com/css2?family=Jost:wght@400;500&family=Tenor+Sans&display=swap" rel="stylesheet">
<style>
:root{
  --navy:#1b2a55;
  --orange:#fc8129;
  --ink:#1f2433;
  --muted:#4a4f5e;
  --line:#e3e6ee;
  --mist:#f7f8fb;
  --white:#ffffff;
}
*{margin:0;padding:0;box-sizing:border-box}
html,body{width:1200px;height:2744px;overflow:hidden;background:var(--white)}
body{position:relative;font-family:'Jost',sans-serif;color:var(--ink)}
.abs{position:absolute}
.display{font-family:'Tenor Sans',sans-serif;font-weight:400;color:var(--navy)}
.brand{display:flex;align-items:center;gap:8px;font-family:'Jost',sans-serif;font-size:21px;color:var(--orange);letter-spacing:.5px}
.brand-dot{width:12px;height:12px;border-radius:50%;background:var(--orange)}
.nav{left:549px;top:80px;display:flex;gap:0;font-size:15px;color:var(--navy)}
.nav span{position:absolute;white-space:nowrap}
.cart{left:1069px;top:68px;width:44px;height:44px;border-radius:50%;background:var(--navy)}
.cart-badge{left:1097px;top:64px;width:15px;height:15px;border-radius:50%;background:var(--orange);color:#fff;font-size:9px;text-align:center;line-height:15px}
.tag{border:1.5px solid var(--orange);color:var(--orange);font-size:11px;font-weight:500;display:flex;align-items:center;padding-left:22px;gap:8px;text-transform:uppercase}
.tag::before{content:"";width:3px;height:3px;border-radius:50%;background:currentColor}
.hero-title{left:88px;top:382px;font-size:40px;line-height:58px}
.hero-copy{left:90px;top:520px;width:400px;font-size:12.5px;line-height:34.4px;color:var(--ink)}
.photo{left:675px;top:255px;width:438px;height:495px;background:linear-gradient(180deg,#f1f2f5 0%,#e7eaf2 40%,#3a4f9e 62%,#2d3c7a 100%)}
.signature{left:1010px;top:223px;font-size:16px;color:var(--orange)}
.mist-band{left:0;top:1243px;width:1200px;height:387px;background:var(--mist)}
.arrow-btn{width:32px;height:32px;border:1.5px solid var(--navy);border-radius:50%}
.card{top:1017px;width:449px;height:334px;background:var(--white);border:1.5px solid var(--line)}
.card-icon{position:absolute;left:48px;top:62px;width:53px;height:53px;border-radius:50%}
.card-title{position:absolute;left:128px;top:70px;font-size:27px;white-space:nowrap}
.card-text{position:absolute;left:52px;top:142px;width:360px;font-size:15.5px;line-height:30px;color:var(--ink)}
.quote-mark{left:109px;top:1530px;width:170px;height:170px;border-radius:50%;background:var(--orange)}
.quote-card{left:361px;top:1468px;width:760px;height:292px;background:var(--white);border-radius:10px;box-shadow:0 20px 50px rgba(27,42,85,.07)}
.quote-text{position:absolute;left:92px;top:90px;font-size:32px;line-height:48px}
.quote-author{position:absolute;left:92px;top:220px;font-size:15px;color:var(--navy)}
.promise{left:0;top:1877px;width:1200px;height:426px;background:var(--orange);overflow:hidden}
.promise-ghost{position:absolute;left:-10px;top:140px;font-family:'Jost',sans-serif;font-size:230px;font-weight:400;color:transparent;-webkit-text-stroke:1.2px rgba(255,255,255,.28);letter-spacing:8px;white-space:nowrap}
.promise .tag{border-color:#fff;color:#fff;text-transform:none}
.promise-title{position:absolute;left:88px;top:185px;font-size:42px;font-weight:500;line-height:58px;color:#fff}
.video{position:absolute;left:600px;top:58px;width:491px;height:310px;background:linear-gradient(120deg,#a39a92 0%,#c7b3a3 45%,#d9a0ac 80%,#f0e6e4 100%)}
.play{position:absolute;left:226px;top:136px;width:38px;height:38px;border-radius:50%;background:#fff}
.foot-head{font-size:13px;font-weight:500;color:var(--navy)}
.foot-list{font-size:13px;color:var(--navy);line-height:29.5px}
.phone-pill{left:624px;top:2516px;width:191px;height:38px;background:#fff;border-radius:6px;box-shadow:0 6px 20px rgba(27,42,85,.08);display:flex;align-items:center;padding-left:14px;gap:8px}
.phone-pill .dot{width:14px;height:14px;border-radius:50%;background:#2bc0c4}
.phone-pill small{font-size:6px;color:var(--muted)}
.phone-pill b{font-size:10px;letter-spacing:2.5px;font-weight:500;color:var(--navy)}
.social{top:2460px;width:44px;height:44px;border-radius:50%;background:var(--navy);color:#fff;font-size:7px;display:flex;align-items:center;justify-content:center}
.social.active{background:var(--orange);box-shadow:0 8px 16px rgba(252,129,41,.35)}
.legal{left:0;width:1200px;text-align:center;color:var(--navy)}
.footer-bg{left:0;top:2303px;width:1200px;height:441px;background:var(--mist)}
</style>
</head>
<body>

<!-- Header -->
<header>
  <div class="abs brand" style="left:88px;top:80px"><span class="brand-dot"></span>Wren of Fabrics</div>
  <nav class="abs nav">
    <span style="left:0">Advice</span>
    <span style="left:77px">Courses</span>
    <span style="left:162px">Quizzes</span>
    <span style="left:244px">Ebooks</span>
    <span style="left:322px">About</span>
    <span style="left:395px">Blog</span>
  </nav>
  <svg class="abs" style="left:1022px;top:83px" width="14" height="14" viewBox="0 0 14 14" fill="none" stroke="#1b2a55" stroke-width="1.5"><circle cx="5.5" cy="5.5" r="4.2"/><path d="M8.7 8.7L13 13"/></svg>
  <div class="abs cart">
    <svg width="44" height="44" viewBox="0 0 44 44" fill="none" stroke="#fff" stroke-width="1.6"><rect x="15" y="18" width="14" height="12" rx="1.5"/><path d="M18.5 18v-2.5a3.5 3.5 0 0 1 7 0V18"/></svg>
  </div>
  <div class="abs cart-badge">1</div>
</header>

<!-- About -->
<section>
  <div class="abs tag" style="left:90px;top:312px;width:133px;height:39px">About me</div>
  <h1 class="abs display hero-title">Daniela Morvak’s here<br>to help all women</h1>
  <p class="abs hero-copy">Daniela Morvak’s clean cut, figure flattering and empowering dresses reflect contemporary classics and the latest trends. Daniela fuses impeccable tailoring and chic styling to create timeless and elegant dresses for every occasion. Made in the UK with luxurious Italian fabrics. Daniela’s innovative online boutique, makes it easy to find unique, elegant styles designed to flatter your body shape.</p>
  <div class="abs photo" role="img" aria-label="Portrait of the stylist in a royal blue blouse and dark scarf"></div>
  <div class="abs signature">Daniela Morvak</div>
</section>

<!-- Mission -->
<div class="abs mist-band"></div>
<section>
  <div class="abs tag" style="left:90px;top:850px;width:108px;height:39px">Mission</div>
  <h2 class="abs display" style="left:86px;top:912px;font-size:40px">Wren of Fabrics mission</h2>
  <div class="abs arrow-btn" style="left:1036px;top:912px">
    <svg width="29" height="29" viewBox="0 0 29 29" fill="none" stroke="#1b2a55" stroke-width="1.3"><path d="M20 14.5H9M12.5 11l-3.5 3.5 3.5 3.5"/></svg>
  </div>
  <div class="abs arrow-btn" style="left:1080px;top:912px">
    <svg width="29" height="29" viewBox="0 0 29 29" fill="none" stroke="#1b2a55" stroke-width="1.3"><path d="M9 14.5h11M16.5 11l3.5 3.5-3.5 3.5"/></svg>
  </div>

  <article class="abs card" style="left:90px">
    <div class="card-icon" style="background:#8ee68a"></div>
    <h3 class="display card-title">Transforming behaviour</h3>
    <p class="card-text">My mission is about transforming customer's shopping behaviours by knowing themselves first before dressing themselves and make smarter decisions for themselves and the environment.</p>
  </article>
  <article class="abs card" style="left:571px">
    <div class="card-icon" style="background:#ee3b3b"></div>
    <h3 class="display card-title">Rewrite fashion rulebook</h3>
    <p class="card-text">I am determined to rewrite the fashion rulebook by educating customers to know themselves first before dressing themselves. Secondly, I want to inspire them to invest in impeccable quality, practical design, and enduring style.</p>
  </article>
  <article class="abs card" style="left:1053px">
    <div class="card-icon" style="background:#fde24f"></div>
    <h3 class="display card-title">Disrupt tradition</h3>
    <p class="card-text">Thirdly I am putting the traditional retail model aside to order concepts with personalisation that dramatically reduce waste.</p>
  </article>
</section>

<!-- Quote -->
<section>
  <div class="abs quote-mark">
    <svg width="170" height="170" viewBox="0 0 170 170" fill="#fff"><path d="M66 68h16v16c0 10-4 18-14 22l-3-6c5-3 7-7 7-11h-6zM91 68h16v16c0 10-4 18-14 22l-3-6c5-3 7-7 7-11h-6z"/></svg>
  </div>
  <blockquote class="abs quote-card">
    <p class="display quote-text">Do the best you can until you know better.<br>Then when you know better, do better</p>
    <cite class="display quote-author" style="font-style:normal">Rosa Ellington</cite>
  </blockquote>
</section>

<!-- Promise -->
<section class="abs promise">
  <div class="promise-ghost" aria-hidden="true">PROMISE</div>
  <div class="abs tag" style="left:91px;top:101px;width:109px;height:39px">Promise</div>
  <h2 class="promise-title">My mission is to<br>empower women !</h2>
  <div class="video" role="img" aria-label="Video still of the stylist speaking beside pink fabric">
    <div class="play">
      <svg width="38" height="38" viewBox="0 0 38 38"><path d="M16 13l9 6-9 6z" fill="#fc8129"/></svg>
    </div>
  </div>
</section>

<!-- Footer -->
<footer>
  <div class="abs footer-bg"></div>
  <div class="abs brand" style="left:88px;top:2414px"><span class="brand-dot"></span>Wren of Fabrics</div>

  <div class="abs" style="left:374px;top:2414px">
    <div class="foot-head">Navigation</div>
    <div class="foot-list" style="margin-top:14px">Home<br>Advice<br>About<br>Contact</div>
  </div>
  <div class="abs" style="left:499px;top:2414px">
    <div class="foot-head">Product</div>
    <div class="foot-list" style="margin-top:14px">Courses<br>Quizzes<br>Ebooks<br>Blog</div>
  </div>
  <div class="abs" style="left:624px;top:2414px">
    <div class="foot-head">Place</div>
    <div class="foot-list" style="margin-top:14px;line-height:27px">12/40 Harbour Rd, Millfield QLD 4102<br>contact@wrenoffabrics.com</div>
  </div>
  <div class="abs phone-pill"><span class="dot"></span><small>Call us on</small><b>0512-774-208</b></div>

  <div class="abs foot-head" style="left:895px;top:2414px">Social Media</div>
  <div class="abs social" style="left:895px">Pagebook</div>
  <div class="abs social active" style="left:957px">Snapgrid</div>
  <div class="abs social" style="left:1013px">Vidtube</div>

  <div class="abs legal" style="top:2678px;font-size:10.5px">
    <svg width="13" height="13" viewBox="0 0 13 13" fill="none" stroke="#1b2a55" style="vertical-align:-2px;margin-right:4px"><circle cx="6.5" cy="6.5" r="5.8"/><path d="M8.4 4.8a2.4 2.4 0 1 0 0 3.4"/></svg>Wren of Fabrics Company - All Rights Reserved
  </div>
  <div class="abs legal" style="top:2698px;font-size:7.5px">Terms &amp; Conditions | Privacy Policy | | Contact Us</div>
</footer>

</body>
</html>
```